Printer Cartridges Supplier Namecard

Attached is my company logo and the design of my current namecard. I would like to have a more special look for it. Can have a little cuteness too rather than those normal standard feel. I'm a supplier mainly dealing with original and compatible printer toner cartridges, some other products like paper supplies as well.

Target Market(s)

Companies, businesses, corporates

Industry/Entity Type

It Company

Contact Information for Business Card

Logo, name, contact, address, supplies and maybe a slogan

Colors
85cae6
33a6d7
3176b5
0255a3
0792cd
85abd2

Requirements
Must have
• Logo, name, contact and address basic details.
• Must include some pictures, not just rearrange what I'm currently having.
Nice to have
• Be creative and bold, a diiferent traditional feel.

```html
<!DOCTYPE html>
<html lang="en">
<head>
<meta charset="utf-8">
<title>tonerbay namecard</title>
<link href="https://fonts.googleapis.com/css2?family=Poppins:wght@300;400;500&display=swap" rel="stylesheet">
<style>
  :root {
    --backdrop: #3a3531;
    --sky: #5fb3e3;
    --ink-grey: #545659;
    --text-dark: #4a4c4f;
    --paper: #ffffff;
  }
  * { margin: 0; padding: 0; box-sizing: border-box; }
  html, body { width: 1200px; height: 930px; overflow: hidden; }
  body {
    background: var(--backdrop);
    font-family: "Poppins", sans-serif;
    position: relative;
  }
  .card {
    position: absolute;
    width: 560px;
    height: 320px;
    border-radius: 18px;
    overflow: hidden;
  }
  .card-front { left: 70px; top: 90px; background: var(--sky); color: var(--paper); }
  .card-back { left: 570px; top: 520px; background: var(--paper); color: var(--text-dark); }

  .brand { position: absolute; display: flex; align-items: center; gap: 12px; }
  .brand-square { border-radius: 8px; }
  .brand-name { font-weight: 300; line-height: 1; letter-spacing: 0.5px; }
  .brand-tagline { position: absolute; font-weight: 400; letter-spacing: 0.2px; white-space: nowrap; }

  .card-front .brand { left: 140px; top: 112px; }
  .card-front .brand-square { width: 44px; height: 44px; background: var(--paper); }
  .card-front .brand-name { font-size: 48px; }
  .card-front .brand-tagline { left: 196px; top: 168px; font-size: 10px; }
  .front-web { position: absolute; left: 0; right: 0; bottom: 32px; text-align: center; font-size: 13px; font-weight: 300; }

  .card-back .brand { left: 36px; top: 112px; }
  .card-back .brand-square { width: 36px; height: 36px; background: var(--sky); }
  .card-back .brand-name { font-size: 40px; color: var(--ink-grey); }
  .card-back .brand-tagline { left: 84px; top: 158px; color: var(--ink-grey); font-size: 8.5px; }

  .divider { position: absolute; left: 300px; top: 36px; width: 1.5px; height: 152px; background: var(--sky); }
  .contact { position: absolute; left: 318px; top: 30px; font-size: 12px; line-height: 1.3; }
  .person-name { color: var(--sky); font-size: 16px; font-weight: 500; letter-spacing: 0.3px; }
  .person-title { font-weight: 400; }
  .hp-label { color: var(--sky); margin-right: 4px; }
  .address { margin-top: 8px; }
  .links { margin-top: 8px; list-style: none; }
  .links li { display: flex; align-items: center; gap: 8px; }
  .links svg { width: 10px; height: 10px; flex: none; }
  .swoosh { position: absolute; left: 0; top: 0; width: 560px; height: 320px; }
</style>
</head>
<body>
  <section class="card card-front" aria-label="Card front">
    <div class="brand">
      <span class="brand-square"></span>
      <span class="brand-name">tonerbay</span>
    </div>
    <p class="brand-tagline">Compatible printer ink and toner solutions</p>
    <p class="front-web">www.tonerbay.sg</p>
  </section>

  <section class="card card-back" aria-label="Card back">
    <svg class="swoosh" viewBox="0 0 560 320" aria-hidden="true">
      <path d="M0,320 L0,310 C120,250 250,260 360,240 C450,224 520,209 560,176 L560,320 Z" fill="#545659"/>
      <path d="M-4,298 C120,238 250,248 360,228 C450,212 520,197 564,162" fill="none" stroke="#5fb3e3" stroke-width="4"/>
    </svg>
    <div class="brand">
      <span class="brand-square"></span>
      <span class="brand-name">tonerbay</span>
    </div>
    <p class="brand-tagline">Compatible printer ink and toner solutions</p>
    <span class="divider"></span>
    <div class="contact">
      <p class="person-name">MAREN TEO</p>
      <p class="person-title">Sales Executive</p>
      <p><span class="hp-label">HP</span>9184 6037</p>
      <p class="address">145A Rivervale Walk<br>06-214 Singapore 541287</p>
      <ul class="links">
        <li><svg viewBox="0 0 10 10"><path d="M2,0.5 L4,2.5 L3,4 Q4.5,6 6,7 L7.5,6 L9.5,8 L8,9.5 Q3,9 0.5,2 Z" fill="#5fb3e3"/></svg>6372-4158</li>
        <li><svg viewBox="0 0 10 10"><rect x="0.5" y="2" width="9" height="6.5" fill="none" stroke="#5fb3e3" stroke-width="1.2"/><path d="M0.5,2 L5,6 L9.5,2" fill="none" stroke="#5fb3e3" stroke-width="1.2"/></svg>maren@tonerbay.sg</li>
        <li><svg viewBox="0 0 10 10"><circle cx="5" cy="5" r="4.4" fill="none" stroke="#5fb3e3" stroke-width="1.1"/><path d="M0.6,5 H9.4 M5,0.6 Q2,5 5,9.4 M5,0.6 Q8,5 5,9.4" fill="none" stroke="#5fb3e3" stroke-width="0.9"/></svg>www.tonerbay.sg</li>
      </ul>
    </div>
  </section>
</body>
</html>
```